American cannabis tech company business card design

Pavrel.com is seeking a modern, professional, and brand-aligned business card that represents our company and its core values: Mission, Story, Values, and Impact. As an innovative cannabis company, we want a business card that is not only visually appealing but also serves as a representation of who we are and what we stand for.

Project Scope: Design a double-sided business card that integrates our brand identity and core values. Incorporate our key brand elements, ensuring a sleek and contemporary aesthetic. Visually reflect our core values (Mission, Story, Values, Impact) in a way that is engaging yet professional.

Target Market(s)

Vendors, third parties,

Contact Information for Business Card

Contact details (name, title, email, phone, website, etc.)

Font styles to use
Other font styles liked:
• Caslon, Centra

Colors

Designer to choose colors to be used in the design.

Requirements
Must have
• Pavrel.com logo and branding A creative yet clean way to integrate our core values (Mission, Story, Values, Impact) Modern typography and a well-structured layout
Nice to have
• forest green, grey, white, black
Should not have
• references to marijuana, leafs, plants, or related product

```html
<!DOCTYPE html>
<html lang="en">
<head>
<meta charset="utf-8">
<title>Pavrel.com Business Card</title>
<link href="https://fonts.googleapis.com/css2?family=Playfair+Display:wght@700;900&family=Montserrat:wght@400;500&display=swap" rel="stylesheet">
<style>
  :root{
    --forest:#183319;
    --forest-deep:#13281a;
    --forest-light:#1f5a30;
    --paper:#ffffff;
    --backdrop:#d3d7d8;
    --ink:#1b1f1c;
  }
  *{margin:0;padding:0;box-sizing:border-box}
  html,body{width:1200px;height:1050px;overflow:hidden}
  body{background:var(--backdrop);position:relative;font-family:"Montserrat",sans-serif}
  .card{position:absolute;width:520px;height:297px;top:376px;box-shadow:0 14px 30px rgba(0,0,0,.18);overflow:hidden}
  .card--front{left:50px;background:var(--paper)}
  .card--back{left:630px;background:var(--forest)}

  .wordmark{position:absolute;left:0;right:0;top:34px;text-align:center;
    font-family:"Playfair Display",serif;font-weight:900;font-size:96px;line-height:1;
    color:var(--forest);letter-spacing:1px}
  .front-band{position:absolute;left:0;bottom:0;width:520px;height:140px}

  .identity{position:absolute;top:158px;left:150px;display:flex;align-items:flex-start;gap:12px}
  .person{text-align:right;padding-top:2px}
  .person__name{font-family:"Playfair Display",serif;font-weight:700;font-size:17px;color:var(--forest)}
  .person__title{font-family:"Playfair Display",serif;font-weight:700;font-size:9px;color:var(--forest);margin-top:1px}
  .divider{width:1px;height:54px;background:var(--ink);margin-top:2px}
  .contacts{list-style:none;font-size:11px;color:var(--ink)}
  .contacts li{display:flex;align-items:center;gap:7px;height:17px}
  .contacts svg{width:9px;height:9px;fill:var(--forest)}

  .back-pattern{position:absolute;inset:0;
    background:linear-gradient(160deg,var(--forest-light) 0%,var(--forest) 40%,var(--forest-deep) 100%)}
  .back-wordmark{position:absolute;right:60px;top:178px;font-family:"Playfair Display",serif;
    font-weight:900;font-size:26px;color:var(--paper);letter-spacing:.5px}
</style>
</head>
<body>
  <section class="card card--front">
    <div class="wordmark">PAVREL</div>
    <svg class="front-band" viewBox="0 0 520 140" aria-hidden="true">
      <path d="M0 40 Q260 150 520 110 L520 140 L0 140 Z" fill="var(--forest)"/>
      <path d="M40 8 Q250 120 480 96 Q250 106 40 8 Z" fill="var(--forest)"/>
    </svg>
    <div class="identity">
      <div class="person">
        <div class="person__name">Daniel Carter</div>
        <div class="person__title">Owner</div>
      </div>
      <div class="divider"></div>
      <ul class="contacts">
        <li><svg viewBox="0 0 10 10"><path d="M2 0.5 L3.6 2.6 L2.8 3.6 Q4 5.8 6.3 7.2 L7.4 6.4 L9.5 8 L8.3 9.5 Q3.5 9 0.5 1.7 Z"/></svg>555-014-0188</li>
        <li><svg viewBox="0 0 10 10"><path d="M0 2 H10 V8 H0 Z M0 2 L5 5.5 L10 2" /></svg>info@pavrel.com</li>
        <li><svg viewBox="0 0 10 10"><circle cx="5" cy="5" r="5"/></svg>www.pavrel.com</li>
      </ul>
    </div>
  </section>

  <section class="card card--back">
    <div class="back-pattern" role="img" aria-label="Repeating brand wordmark pattern in green tones"></div>
    <div class="back-wordmark">PAVREL</div>
  </section>
</body>
</html>
```